Real Estate Company / Capital Needs Cards!

need business cards designed using the logos that were just designed by pixelbarn.

Reason: per designers request deadline extended 1 day…thank you.

Target Market(s)

Investors and clients looking to purchase real estate or invest in the business.

Industry/Entity Type

Business

Requirements
Must have
• two designs - one for the real estate logo and one for the capital logo, similar but slightly different.
Nice to have
• something to make it pop (perhaps on the back)
Should not have
• much color

```html
<!DOCTYPE html>
<html lang="en">
<head>
<meta charset="utf-8">
<title>Marlow Real Estate – Business Cards</title>
<link href="https://fonts.googleapis.com/css2?family=Cinzel:wght@400;700&family=Open+Sans:wght@400;600&display=swap" rel="stylesheet">
<style>
  :root {
    --backdrop: #6b4428;
    --card: #ffffff;
    --ink: #3f3f42;
    --ink-soft: #7a7a7e;
    --mark: #8d8d91;
    --band-light: #cfcfd1;
    --band-dark: #747478;
    --rule: #d4d4d6;
  }
  * { margin: 0; padding: 0; box-sizing: border-box; }
  html, body { width: 1200px; height: 498px; overflow: hidden; }
  body {
    background: var(--backdrop);
    position: relative;
    font-family: "Open Sans", Arial, sans-serif;
    color: var(--ink);
  }
  .card {
    position: absolute;
    top: 99px;
    width: 530px;
    height: 300px;
    background: var(--card);
    box-shadow: 0 6px 18px rgba(0,0,0,.35);
    overflow: hidden;
  }
  .card--front { left: 45px; }
  .card--back { left: 625px; }

  .brand { display: flex; align-items: center; gap: 10px; color: var(--mark); font-family: "Cinzel", Georgia, serif; font-weight: 400; }
  .brand__square { background: var(--mark); flex: none; }
  .brand__name { line-height: 1.05; }
  .brand__name span { display: block; }

  .card--front .brand { position: absolute; left: 40px; top: 112px; }
  .card--front .brand__square { width: 34px; height: 34px; }
  .card--front .brand__name span:first-child { font-size: 31px; letter-spacing: 1px; }
  .card--front .brand__name span:last-child { font-size: 13px; letter-spacing: 3px; }

  .divider { position: absolute; left: 246px; top: 32px; width: 1px; height: 120px; background: var(--rule); }

  .contact { position: absolute; left: 262px; top: 32px; list-style: none; font-size: 13.5px; line-height: 1.45; }
  .contact li { display: flex; align-items: center; gap: 5px; }
  .contact .contact__phone { font-size: 16px; margin-top: 3px; }
  .contact .contact__email { font-size: 13.5px; margin-top: 3px; }
  .contact svg { width: 12px; height: 12px; fill: var(--ink); flex: none; }

  .bands { position: absolute; left: 0; bottom: 0; width: 530px; height: 110px; }
  .band-light { fill: var(--band-light); }
  .band-dark { fill: var(--band-dark); }

  .holder { position: absolute; right: 42px; bottom: 52px; font-family: "Cinzel", Georgia, serif; font-size: 17px; letter-spacing: .5px; }
  .holder__name { font-weight: 700; color: var(--ink); }
  .holder__title { font-weight: 400; color: var(--ink-soft); }

  .card--back .brand { position: absolute; left: 90px; top: 78px; gap: 20px; }
  .card--back .brand__square { width: 80px; height: 80px; }
  .card--back .brand__name span:first-child { font-size: 64px; letter-spacing: 2px; }
  .card--back .brand__name span:last-child { font-size: 26px; letter-spacing: 5px; }

  .website { position: absolute; left: 0; right: 0; top: 222px; text-align: center; font-size: 15px; letter-spacing: 3px; color: var(--ink); }
  .website b { font-weight: 600; }
</style>
</head>
<body>
  <section class="card card--front">
    <div class="brand">
      <div class="brand__square"></div>
      <div class="brand__name"><span>MARLOW</span><span>REAL ESTATE</span></div>
    </div>
    <div class="divider"></div>
    <ul class="contact">
      <li>Street Name, City Name</li>
      <li>State ZipCode</li>
      <li class="contact__phone">
        <svg viewBox="0 0 24 24"><path d="M6.6 10.8a15 15 0 0 0 6.6 6.6l2.2-2.2a1 1 0 0 1 1-.25 11.4 11.4 0 0 0 3.6.57 1 1 0 0 1 1 1V20a1 1 0 0 1-1 1A17 17 0 0 1 3 4a1 1 0 0 1 1-1h3.5a1 1 0 0 1 1 1c0 1.25.2 2.45.57 3.57a1 1 0 0 1-.25 1z"/></svg>123-456-7980
      </li>
      <li class="contact__phone">
        <svg viewBox="0 0 24 24"><path d="M8 1h8a2 2 0 0 1 2 2v18a2 2 0 0 1-2 2H8a2 2 0 0 1-2-2V3a2 2 0 0 1 2-2zm0 3v14h8V4zm4 15.5a1 1 0 1 0 0 2 1 1 0 0 0 0-2z"/></svg>123-568-7896
      </li>
      <li class="contact__email">
        <svg viewBox="0 0 24 24"><path d="M2 5h20v14H2zm2 2v.5l8 5 8-5V7zm0 2.8V17h16V9.8l-8 5z"/></svg>hello@marlowrealestate.com
      </li>
    </ul>
    <svg class="bands" viewBox="0 0 530 110" preserveAspectRatio="none" aria-hidden="true">
      <polygon class="band-light" points="300,55 530,28 530,110 0,110 0,95 280,75"/>
      <polygon class="band-dark" points="0,80 260,62 252,76 0,95"/>
      <polygon class="band-light" points="0,98 530,98 530,110 0,110"/>
    </svg>
    <p class="holder"><span class="holder__name">YOUR NAME,</span> <span class="holder__title">TITLE</span></p>
  </section>

  <section class="card card--back">
    <div class="brand">
      <div class="brand__square"></div>
      <div class="brand__name"><span>MARLOW</span><span>REAL ESTATE</span></div>
    </div>
    <p class="website">www.<b>marlowrealestate</b>.com</p>
  </section>
</body>
</html>
```